Business Card Design For A Cajun Seafood Restaurant

We are opening a cajun seafood restaurant in a week. We mainly serve cajun seafood which is orginally from Louisiana. We want design on both sides of a business card. I have menu on the website. You can go to www.reednkettle.example to check out our menu.

Restaurant name: Reed N' Kettle
Phone: +1 (555) 304-7712
Address: 48206 Ludlow Row, #7, Bexmoor Flats, Ca90000
Email: reednkettle@mailbox.example
Website: www.reednkettle.example

Maybe add social media icons (facebook, instagram) if looks nice on the business card.
facebook.com/reednkettle
instagram.com/reednkettle or @reednkettle

Attached is the logo and other business card samples that I like.

```html
<!DOCTYPE html>
<html lang="en">
<head>
<meta charset="utf-8">
<title>Reed N' Kettle – Business Card</title>
<link href="https://fonts.googleapis.com/css2?family=Roboto:wght@400;500;700&display=swap" rel="stylesheet">
<style>
  :root {
    --backdrop: #e4e4e4;
    --card-white: #f7f7f7;
    --brand-yellow: #f0c215;
    --brand-yellow-deep: #e2b30c;
    --brand-orange: #d9622a;
    --mascot-orange: #e2672e;
    --ink: #1b1b1b;
    --ink-soft: #333333;
    --rule: #d2d2d2;
    --white: #ffffff;
  }
  * { margin: 0; padding: 0; box-sizing: border-box; }
  html, body {
    width: 1200px; height: 576px; overflow: hidden;
    background: var(--backdrop);
    font-family: "Roboto", Arial, sans-serif;
  }
  .canvas { position: relative; width: 1200px; height: 576px; }

  .card {
    position: absolute; top: 139px;
    width: 484px; height: 293px;
    border-radius: 6px; overflow: hidden;
    box-shadow: 0 3px 6px rgba(0,0,0,0.25);
  }

  /* Front */
  .card-front { left: 82px; background: var(--brand-yellow); }
  .front-photo {
    position: absolute; inset: 0;
    background: radial-gradient(ellipse at 40% 45%, var(--brand-yellow) 0%, var(--brand-yellow-deep) 70%, #d9a90a 100%);
  }
  .front-brand {
    position: absolute; left: 0; right: 0; top: 0; bottom: 0;
    display: flex; flex-direction: column; align-items: center; justify-content: center; gap: 14px;
  }
  .brand-mark {
    width: 96px; height: 96px; border-radius: 50%;
    background: var(--mascot-orange);
  }
  .brand-name {
    font-size: 30px; font-weight: 700; color: var(--ink);
    letter-spacing: 1px; text-transform: uppercase;
  }

  /* Back */
  .card-back { left: 602px; background: var(--card-white); }
  .back-mark {
    position: absolute; left: 46px; top: 70px;
    width: 160px; height: 140px;
    display: flex; align-items: center; justify-content: center;
  }
  .back-mark .brand-name { font-size: 22px; color: var(--mascot-orange); text-align: center; line-height: 1.2; }
  .divider {
    position: absolute; left: 245px; top: 61px;
    width: 1px; height: 144px; background: var(--rule);
  }
  .contact { position: absolute; left: 273px; top: 60px; color: var(--ink-soft); }
  .person-name { font-size: 21px; font-weight: 700; color: var(--ink); line-height: 1.1; }
  .person-role { font-size: 11px; margin-top: 2px; }
  .address { font-size: 13px; line-height: 18px; margin-top: 14px; }
  .contact-list { list-style: none; margin-top: 6px; font-size: 13px; line-height: 18px; }
  .contact-list li { display: flex; align-items: center; gap: 8px; }
  .contact-list svg { width: 11px; height: 11px; fill: var(--ink); flex: none; }

  .bands { position: absolute; left: 0; bottom: 0; width: 484px; height: 40px; }
  .social {
    position: absolute; left: 273px; bottom: 13px;
    display: flex; align-items: center; gap: 6px;
    font-size: 13px; color: var(--white);
  }
  .social-dot { width: 10px; height: 10px; border-radius: 2px; background: var(--white); opacity: 0.85; }
  .social-gap { width: 4px; }
</style>
</head>
<body>
<main class="canvas">

  <section class="card card-front">
    <div class="front-photo" role="img" aria-label="Faint photograph of corn cobs and boiled crab, tinted yellow"></div>
    <div class="front-brand">
      <div class="brand-mark" role="img" aria-label="Restaurant mascot illustration"></div>
      <div class="brand-name">Reed N' Kettle</div>
    </div>
  </section>

  <section class="card card-back">
    <div class="back-mark"><div class="brand-name">Reed N' Kettle</div></div>
    <div class="divider"></div>
    <div class="contact">
      <h1 class="person-name">Alan Prewitt</h1>
      <p class="person-role">Director</p>
      <p class="address">48206 Ludlow Row, #7,<br>Bexmoor Flats, Ca90000</p>
      <ul class="contact-list">
        <li><svg viewBox="0 0 12 12"><path d="M1 3c0-1 1-2 5-2s5 1 5 2v1H8V3H4v1H1zM3 5h6l2 5H1z"/></svg>+1 (555) 304-7712</li>
        <li><svg viewBox="0 0 12 12"><path d="M1 2h10v8H1zM1 2l5 4 5-4" stroke="#fff" stroke-width="1"/></svg>reednkettle@mailbox.example</li>
        <li><svg viewBox="0 0 12 12"><circle cx="6" cy="6" r="5"/><path d="M1 6h10M6 1v10" stroke="#fff" stroke-width="0.8"/></svg>www.reednkettle.example</li>
      </ul>
    </div>
    <svg class="bands" viewBox="0 0 484 40" preserveAspectRatio="none" aria-hidden="true">
      <polygon points="0,17 238,17 224,40 0,40" fill="var(--brand-yellow-deep)"/>
      <polygon points="246,2 484,2 484,40 224,40" fill="var(--brand-orange)"/>
    </svg>
    <div class="social">
      <span class="social-dot"></span><span>/reednkettle</span>
      <span class="social-gap"></span>
      <span class="social-dot"></span><span>@reednkettle</span>
    </div>
  </section>

</main>
</body>
</html>
```